German Headhunter/ HR Consultancy needs Business Cards Design

We need a business Card Design for our Company in Stuttgart. We are specialized as Headhunter/ HR Consultancy in Placement of specialist and managers in permanent employment. Please refer to our business logo.

```html
<!DOCTYPE html>
<html lang="de">
<head>
<meta charset="utf-8">
<title>Kernwerk Personalberatung – Visitenkarte</title>
<link rel="stylesheet" href="https://fonts.googleapis.com/css2?family=Montserrat:wght@600&family=Arimo:wght@400&display=swap">
<style>
  :root {
    --page-bg: #e9e7e6;
    --card-blue: #3a54a5;
    --card-grey: #96969b;
    --text-white: #ffffff;
    --brand-blue: #3a54a5;
    --window-light: #f4f2f2;
    --window-mid: #dcd6d6;
    --window-edge: #c9c2c4;
  }
  html, body {
    margin: 0;
    width: 1200px;
    height: 900px;
    overflow: hidden;
    background: var(--page-bg);
  }
  .canvas {
    position: relative;
    width: 1200px;
    height: 900px;
  }
  .business-card {
    position: absolute;
    left: 100px;
    top: 141px;
    width: 1000px;
    height: 617px;
    background: var(--card-grey);
    overflow: hidden;
    box-shadow: 0 10px 30px rgba(0,0,0,0.15);
  }
  .blue-panel {
    position: absolute;
    left: 0;
    top: 0;
    width: 678px;
    height: 100%;
    background: var(--card-blue);
  }
  .contact-block {
    position: absolute;
    left: 59px;
    color: var(--text-white);
    font-family: "Arimo", Arial, sans-serif;
  }
  .holder-name {
    position: absolute;
    left: 59px;
    top: 65px;
    margin: 0;
    color: var(--text-white);
    font-family: "Montserrat", sans-serif;
    font-weight: 600;
    font-size: 42px;
    letter-spacing: -0.5px;
    line-height: 1;
  }
  .holder-role {
    position: absolute;
    left: 58px;
    top: 111px;
    margin: 0;
    color: var(--text-white);
    font-family: "Arimo", Arial, sans-serif;
    font-size: 28px;
    line-height: 1;
  }
  .address {
    top: 250px;
    margin: 0;
    font-size: 29.5px;
    line-height: 36.5px;
    font-style: normal;
  }
  .contact-list {
    top: 443px;
    margin: 0;
    padding: 0;
    list-style: none;
    font-size: 29.5px;
    line-height: 36.5px;
  }
  .contact-list li {
    display: flex;
    align-items: center;
    gap: 8px;
  }
  .contact-icon {
    width: 27px;
    height: 27px;
    flex: none;
  }
  .brand-window {
    position: absolute;
    left: 412px;
    top: 41px;
    width: 532px;
    height: 532px;
    border-radius: 50%;
    background: radial-gradient(circle at 50% 40%, var(--window-light) 0%, var(--window-mid) 70%, var(--window-edge) 100%);
  }
  .brand-name {
    position: absolute;
    left: 0;
    right: 0;
    top: 222px;
    margin: 0;
    text-align: center;
    color: var(--brand-blue);
    font-family: "Montserrat", sans-serif;
    font-weight: 600;
    line-height: 1;
  }
  .brand-name .brand-main {
    display: block;
    font-size: 54px;
    letter-spacing: 1px;
  }
  .brand-name .brand-sub {
    display: block;
    margin-top: 8px;
    font-size: 22px;
    letter-spacing: 0.5px;
  }
</style>
</head>
<body>
<main class="canvas">
  <section class="business-card" aria-label="Visitenkarte Kernwerk Personalberatung">
    <div class="blue-panel"></div>

    <h1 class="holder-name">LUKAS BRENNER</h1>
    <p class="holder-role">Managing Director</p>

    <address class="contact-block address">
      42, Königstraße<br>
      Innenstadt<br>
      70173,Stuttgart
    </address>

    <ul class="contact-block contact-list">
      <li>
        <svg class="contact-icon" viewBox="0 0 24 24" aria-hidden="true">
          <path fill="#fff" d="M6.6 10.8c1.4 2.8 3.8 5.1 6.6 6.6l2.2-2.2c.3-.3.7-.4 1-.2 1.1.4 2.3.6 3.6.6.6 0 1 .4 1 1V20c0 .6-.4 1-1 1C10.6 21 3 13.4 3 4c0-.6.4-1 1-1h3.5c.6 0 1 .4 1 1 0 1.3.2 2.5.6 3.6.1.3 0 .7-.2 1z"/>
          <path fill="none" stroke="#fff" stroke-width="1.6" d="M14 3.5a7 7 0 0 1 6.5 6.5M14 7a3.5 3.5 0 0 1 3 3"/>
        </svg>
        <span>0711-234 567 890</span>
      </li>
      <li>
        <svg class="contact-icon" viewBox="0 0 24 24" aria-hidden="true">
          <rect x="1.5" y="5" width="21" height="14" fill="#fff"/>
          <path fill="none" stroke="#3a54a5" stroke-width="1.4" d="M1.5 5l10.5 8 10.5-8M1.5 19l8-7M22.5 19l-8-7"/>
        </svg>
        <span>info@kernwerk.de</span>
      </li>
      <li>
        <svg class="contact-icon" viewBox="0 0 24 24" aria-hidden="true">
          <g fill="none" stroke="#fff" stroke-width="1.6">
            <circle cx="12" cy="12" r="10"/>
            <ellipse cx="12" cy="12" rx="4.5" ry="10"/>
            <path d="M2 12h20M4 6.5h16M4 17.5h16"/>
          </g>
        </svg>
        <span>www.kernwerk.de</span>
      </li>
    </ul>

    <div class="brand-window" role="img" aria-label="Klarsichtfenster im Kartenmaterial">
      <p class="brand-name">
        <span class="brand-main">KERNWERK</span>
        <span class="brand-sub">PERSONALBERATUNG</span>
      </p>
    </div>
  </section>
</main>
</body>
</html>
```